Deodorant Product Sales One Pager and Annexes

Schedule: Very short deadline - to be complete within 12 hours
Budget: 2-3 hours
Format: Adobe Illustrator / A4 landscape or portrait - for submission by email in PDF
OBJECTIVE
We need a one pager sales sheet and its annexes to present a new deodorant range to the largest supermarket chain in Australia. This is a very important submission that can create more design projects for you. Please refer to the attachments for a starting point. We need to keep the design minimalist and elegant, stylish, clean and chic IN KEEPING WITH THE 1.618 ratio. Styles to avoid are too bright colors, clutter, comic or gimmicky styles. Please maintain a sense of high quality design and professionalism as this is a premium product in Australia.
TARGET AUDIENCE
Senior buyer of largest supermarket chain in Australia
Attachments:
Product one pager
Annexes to one pager
Product shots in low and high resolution
Target Market(s)
Senior cosmetics buyer at Australia's largest supermarket chain
Industry/Entity Type
Landscape

```html
<!DOCTYPE html>
<html lang="en">
<head>
<meta charset="utf-8">
<title>The Magnesium Trend</title>
<link href="https://fonts.googleapis.com/css2?family=Bitter:ital,wght@0,300;0,400;0,700;1,400;1,700&display=swap" rel="stylesheet">
<style>
  :root {
    --ink: #3b4855;
    --ink-soft: #5b6c7b;
    --paper: #ffffff;
    --chart-line: #3a73e8;
    --chart-grid: #ececec;
    --chart-text: #8a8f95;
    --chart-dark: #222222;
  }
  html, body {
    margin: 0;
    padding: 0;
    overflow: hidden;
    background: var(--paper);
  }
  .sheet {
    position: relative;
    width: 1200px;
    height: 849px;
    background: var(--paper);
    color: var(--ink);
    font-family: "Bitter", Georgia, serif;
    overflow: hidden;
  }
  .trend-title {
    position: absolute;
    left: 329px;
    top: 176px;
    margin: 0;
    font-size: 16px;
    font-weight: 700;
    font-style: italic;
    letter-spacing: -0.2px;
  }
  .trend-subtitle {
    position: absolute;
    left: 329px;
    top: 218px;
    margin: 0;
    font-size: 16px;
    font-weight: 400;
    font-style: italic;
    color: var(--ink-soft);
  }
  .trend-chart {
    position: absolute;
    left: 329px;
    top: 271px;
    width: 543px;
    height: 257px;
  }
  .chart-source {
    position: absolute;
    left: 329px;
    top: 529px;
    margin: 0;
    font-size: 11px;
    font-weight: 700;
    font-style: italic;
    color: var(--ink-soft);
  }
  .market-quote {
    position: absolute;
    left: 329px;
    top: 584px;
    width: 560px;
    margin: 0;
  }
  .market-quote p {
    margin: 0;
    font-size: 15.5px;
    font-weight: 300;
    line-height: 21px;
    color: var(--ink);
  }
  .market-quote footer {
    margin-top: 2px;
    font-size: 12.5px;
    font-weight: 700;
    font-style: italic;
    line-height: 17px;
    color: var(--ink-soft);
  }
  .brand-name {
    position: absolute;
    left: 992px;
    top: 735px;
    margin: 0;
    font-size: 29px;
    font-weight: 700;
    color: var(--ink-soft);
    letter-spacing: -0.5px;
  }
</style>
</head>
<body>
<main class="sheet">
  <h1 class="trend-title">The Magnesium Trend</h1>
  <h2 class="trend-subtitle">Seekwell search interest for magnesium supplements increases by 200%</h2>

  <svg class="trend-chart" viewBox="231 190 381 180" role="img" aria-label="Line chart of web search interest for magnesium supplements in Australia, July 2011 to January 2013">
    <text x="232" y="201" font-family="Arial, sans-serif" font-size="6.2" fill="var(--chart-text)">Web Search Interest: <tspan font-weight="700" fill="#666">"magnesium supplement"</tspan>. Australia, Jul 2011 - Jan 2013.</text>
    <rect x="489" y="195" width="6" height="6" fill="#f2c4cc"/>
    <rect x="572" y="191" width="35" height="14" rx="2" fill="#f5f5f5" stroke="#dcdcdc" stroke-width="0.6"/>
    <circle cx="586" cy="198" r="2.6" fill="none" stroke="#555" stroke-width="1.4"/>
    <path d="M599 197 l2 2 l2 -2" fill="#555"/>
    <line x1="231" y1="210" x2="612" y2="210" stroke="var(--chart-grid)" stroke-width="0.8"/>

    <text x="232" y="232" font-family="Arial, sans-serif" font-size="6.4" font-weight="700" fill="var(--chart-dark)">Interest over time</text>
    <circle cx="298" cy="230" r="2.6" fill="none" stroke="#ccc" stroke-width="0.5"/>
    <text x="232" y="242" font-family="Arial, sans-serif" font-size="5.2" fill="var(--chart-dark)">The number 100 represents the peak search interest</text>
    <text x="508" y="241" font-family="Arial, sans-serif" font-size="5" fill="#bcc8d4">News headlines</text>
    <circle cx="551" cy="239" r="2.4" fill="none" stroke="#ccc" stroke-width="0.5"/>
    <text x="573" y="241" font-family="Arial, sans-serif" font-size="5" fill="#bcc8d4">Forecast</text>
    <circle cx="600" cy="239" r="2.4" fill="none" stroke="#ccc" stroke-width="0.5"/>
    <line x1="231" y1="246" x2="612" y2="246" stroke="var(--chart-grid)" stroke-width="0.8"/>

    <g stroke="var(--chart-grid)" stroke-width="0.6">
      <line x1="231" y1="268" x2="612" y2="268"/>
      <line x1="231" y1="286" x2="612" y2="286"/>
      <line x1="231" y1="304" x2="612" y2="304"/>
      <line x1="231" y1="322" x2="612" y2="322"/>
      <line x1="231" y1="340" x2="612" y2="340"/>
      <line x1="231" y1="357" x2="612" y2="357" stroke="#d6d6d6"/>
    </g>
    <g font-family="Arial, sans-serif" font-size="4" fill="var(--chart-text)">
      <text x="233" y="271">100</text>
      <text x="233" y="289">80</text>
      <text x="233" y="307">60</text>
      <text x="233" y="325">40</text>
      <text x="233" y="343">20</text>
    </g>
    <polyline fill="none" stroke="var(--chart-line)" stroke-width="1.1" stroke-linejoin="round"
      points="232,357 251,288 272,318 293,309 314,319 335,312 356,302 377,314 398,311 418,298 438,317 459,304 480,325 501,299 521,308 542,272 563,292 584,312 605,265"/>
    <g font-family="Arial, sans-serif" font-size="4" fill="var(--chart-text)" text-anchor="middle">
      <text x="284" y="364">Oct 2011</text>
      <text x="346" y="364">Jan 2012</text>
      <text x="408" y="364">Apr 2012</text>
      <text x="469" y="364">Jul 2012</text>
      <text x="532" y="364">Oct 2012</text>
      <text x="594" y="364">Jan 2013</text>
    </g>
  </svg>

  <p class="chart-source">Source: Seekwell Trends 2013</p>

  <blockquote class="market-quote">
    <p>‘The magnesium market is second only to calcium, currently, but it has the potential to exceed the calcium market.’</p>
    <footer>Lena Varga<br>Director, Corvel Mineral Health</footer>
  </blockquote>

  <p class="brand-name">velmora</p>
</main>
</body>
</html>
```